Modern, clean and professional Wordpress design for a safety training company!

We are currently in the process of creating a new website for our business. We have hired a website developer and the main structure of our new Wordpress site is complete. We now need an overall design plan for the site. We need a very clean, professional and easy to follow website. Most of our website visitors only spend about 30-45 secs on our sites "shopping " so it is imperative that we have a strong Home Page.
Our company specializes in CPR and First Aid Certification Classes to businesses and individuals throughout Northern California. We provide these certifications two ways: ONSITE-We come to you, and HOSTED-we offer weekly classes at our 2 locations.
Our design needs to use the general green and blue colors of our logo. But we also like white.
The final design MUST communicate a legitimate, trustworthy and professional business. Our industry is VERY competitive and we need to STAND OUT.
Currently, the NEW website that we need a new design for is www.LifelineDrillWorks.com
Our old website is www.RescuePrepValleyHub.com and we really do like the design of this website, but we just needed a Wordpress site for SEO purposes.
These are 3 websites that we really:
http://morvaliontech.com/
http://www.tralbex.com/
https://www.plivant.com/
I have attached our Logo and other images if you need to use them but looking at the current two sites will be you best help.
Target Market(s)
1) Large businesses and industries that are looking for a company to provide ONSITE safety training classes at their office or place of work.
2) Individuals that need certifications for their jobs and other needs. These individuals are looking for a legitimate, trustworthy and professional environment to complete their training class.

```html
<!DOCTYPE html>
<html lang="en">
<head>
<meta charset="utf-8">
<title>Valewick Response Academy</title>
<link href="https://fonts.googleapis.com/css2?family=Open+Sans:ital,wght@0,400;0,600;0,700;1,400&family=Shadows+Into+Light&display=swap" rel="stylesheet">
<style>
:root{
  --green:#8cb30f;
  --green-dark:#7ea10c;
  --navy:#1c3a8a;
  --blue:#2f8fd6;
  --ink:#333;
  --muted:#777;
  --rule:#e6e6e6;
  --footer:#2b2b2b;
  --footer-text:#cfcfcf;
}
*{margin:0;padding:0;box-sizing:border-box}
html,body{width:750px;height:1200px;overflow:hidden;background:#fff}
body{font-family:'Open Sans',Arial,sans-serif;color:var(--ink);position:relative}
.abs{position:absolute}
.topline{left:0;top:0;width:750px;height:2px;background:var(--green)}
.brand{left:62px;top:22px;display:flex;align-items:center;gap:8px}
.brand-dot{width:26px;height:26px;border-radius:50%;background:var(--green)}
.brand-name{font-size:13px;font-weight:700;color:var(--navy);line-height:1.15;width:110px}
.freecall{right:62px;top:16px;font-size:11.5px;font-weight:700;color:var(--navy)}
.freecall span{color:var(--green);font-weight:600}
.nav{left:207px;top:39px;display:flex;align-items:center;height:26px;font-size:7.5px;text-transform:uppercase;color:#444}
.nav a{text-decoration:none;color:inherit;padding:0 14.5px;line-height:26px}
.nav a.active{background:var(--green);color:#fff;padding:0 16px;margin-right:0}
.hero{left:0;top:83px;width:750px;height:421px;background:linear-gradient(180deg,#b9b4ab 0%,#6d6152 40%,#3a2f26 100%)}
.arrow{top:251px;width:22px;height:28px;background:rgba(0,0,0,.55);display:flex;align-items:center;justify-content:center}
.headline{left:0;top:288px;width:750px;text-align:center;color:#fff;font-weight:700;font-size:14.5px;line-height:19px}
.headline em{font-style:normal;color:var(--green)}
.promo{top:366px;width:208px;height:138px;padding:20px 22px;color:#fff}
.promo h3{font-size:11px;font-weight:600;margin-bottom:12px}
.promo p{font-size:7.2px;line-height:12px}
.promo strong{display:block;font-size:9.5px;margin-top:2px}
.promo .btn-outline{position:absolute;left:23px;top:95px;width:69px;height:23px;border:1.5px solid #fff;font-size:7px;font-weight:600;display:flex;align-items:center;justify-content:center}
.p1{left:63px;background:rgba(12,56,170,.85)}
.p2{left:271px;background:rgba(140,185,15,.92)}
.p3{left:479px;background:rgba(40,150,220,.9)}
.welcome{left:0;top:524px;width:750px;text-align:center;font-size:14px}
.welcome b{color:var(--green);font-weight:600}
.intro{left:130px;top:553px;width:490px;text-align:center;font-size:8.6px;line-height:13.5px;color:var(--muted)}
.rule{left:62px;width:626px;height:1px;background:var(--rule)}
.photo{top:619px;height:129px;border:2px solid #eee}
.service h2{font-size:14px;font-weight:400;color:#222}
.service h2 b{color:var(--green);font-weight:600}
.service p{font-size:7.5px;line-height:13.5px;color:var(--muted);margin-top:9px;width:300px}
.btn{position:absolute;top:838px;width:66px;height:26px;background:var(--green);color:#fff;font-size:7.8px;display:flex;align-items:center;justify-content:center}
.stars{left:0;top:912px;width:750px;display:flex;justify-content:center;gap:2px}
.quote{left:130px;top:934px;width:490px;text-align:center;font-style:italic;font-size:9px;line-height:16px;color:#555}
.author{left:0;top:968px;width:750px;text-align:center;font-family:'Shadows Into Light',cursive;color:var(--green);font-size:13px}
.avatars{left:70px;top:998px;width:610px;height:27px;background:linear-gradient(90deg,#e7d4c6,#a77e68,#d9b59d,#6b4f42,#c79f86,#eadbd0)}
.footer{left:0;top:1066px;width:750px;height:134px;background:var(--footer);color:var(--footer-text)}
.footer h4{position:absolute;top:16px;font-size:10.5px;font-weight:400;color:#fff;text-transform:uppercase}
.footer p{position:absolute;top:44px;font-size:7.5px;line-height:14px}
.flogo{left:62px;top:20px;display:flex;align-items:center;gap:6px;opacity:.35}
.flogo span{font-size:10px;font-weight:700;color:#888;width:80px;line-height:1.15}
.social{position:absolute;left:560px;top:36px;display:flex;gap:5px}
.social i{width:22px;height:22px;border-radius:50%;display:block}
.frule{position:absolute;left:0;top:89px;width:750px;height:1px;background:#3a3a3a}
.copy{position:absolute;left:62px;top:107px;font-size:7px}
.flinks{position:absolute;left:333px;top:107px;font-size:7px;display:flex;gap:9px}
.code{position:absolute;left:716px;top:102px;font-size:6.5px}
.bottomline{left:0;top:1197px;width:750px;height:3px;background:var(--green)}
</style>
</head>
<body>
<div class="abs topline"></div>

<header>
  <div class="abs brand"><span class="brand-dot"></span><span class="brand-name">Valewick Response Academy</span></div>
  <div class="abs freecall">FREECALL <span>916-555-0172</span></div>
  <nav class="abs nav">
    <a class="active">Home</a><a>Class Calender</a><a>Classes for Groups</a><a>Certification Classes</a><a>About Us</a><a>Policies</a>
  </nav>
</header>

<section class="abs hero" role="img" aria-label="Photo of a classroom full of students facing an instructor at a whiteboard"></section>
<div class="abs arrow" style="left:0"><svg width="8" height="12"><path d="M7 1L2 6l5 5" stroke="#fff" stroke-width="1.6" fill="none"/></svg></div>
<div class="abs arrow" style="right:0;background:none"><svg width="8" height="12"><path d="M1 1l5 5-5 5" stroke="#fff" stroke-width="1.6" fill="none"/></svg></div>
<div class="abs headline">Stop wasting time and money with those long, expensive <em>CPR</em><br><em>CLASSES!</em> Try the Academy and you'll never go back to your old class!</div>

<div class="abs promo p1"><h3>First Aid Certification Classes</h3><p>Aliquam ornare, magna id gravida iaculis, sapien velit sodales urna, a pretium est nulla a nibh. Fusce ac aliquet metus.</p><span class="btn-outline">READ MORE</span></div>
<div class="abs promo p2"><h3>Register and Pay Online (CPR)</h3><p>Aliquam ornare, magna id gravida iaculis, sapien velit sodales urna, a pretium est nulla a nibh.</p><strong>$39 Adult/Child/Infant 90 Minutes!</strong><span class="btn-outline">REGISTER</span></div>
<div class="abs promo p3"><h3>Register and Pay Online (BLS)</h3><p>Aliquam ornare, magna id gravida iaculis, sapien velit sodales urna, a pretium est nulla a nibh.</p><strong>$39 Adult/Child/Infant 90 Minutes!</strong><span class="btn-outline">REGISTER</span></div>

<h1 class="abs welcome"><b>WELCOME</b>&nbsp; to Valewick Response Academy!</h1>
<p class="abs intro">Valewick Response Academy is Northern California's leader in CPR, BLS, and Basic First Aid Certifications! Taught by experienced Firefighters, our classes are much shorter and provide common sense knowledge and skills .</p>
<div class="abs rule" style="top:598px"></div>

<div class="abs photo" style="left:62px;width:301px;background:linear-gradient(135deg,#6a7fb8,#4d5f9a 50%,#a78f86)" role="img" aria-label="Photo of medical staff in scrubs practicing a procedure"></div>
<div class="abs photo" style="left:386px;width:302px;background:linear-gradient(180deg,#8b8a86,#4a4a4a 55%,#c8bfb8)" role="img" aria-label="Photo of CPR training mannequins on a classroom table"></div>

<div class="abs service" style="left:61px;top:760px"><h2><b>ONSITE</b>-We Come to You</h2><p>Aliquam erat volutpat. Ut wisi enim ad minim veniam, quis nolorem kastrud exerci tation ullamcorper suscipit lobortis nisl ut aliquip exlorem ea commodo conseqrper suscipit lobortis nisl ut aliquat.</p></div>
<div class="abs service" style="left:388px;top:760px"><h2><b>HOSTED</b>-we offer weekly classes</h2><p>Aliquam erat volutpat. Ut wisi enim ad minim veniam, quis nolorem kastrud exerci tation ullamcorper suscipit lobortis nisl ut aliquip exlorem ea commodo conseqrper suscipit lobortis nisl ut aliquat.</p></div>
<span class="btn" style="left:62px">READ MORE</span>
<span class="btn" style="left:386px">READ MORE</span>
<div class="abs rule" style="top:898px"></div>

<div class="abs stars">
  <svg width="80" height="14" viewBox="0 0 80 14"><g fill="#f0b323" stroke="#b57d10" stroke-width=".6">
  <path id="s" d="M7 .8l1.9 4.2 4.5.4-3.4 3 1 4.5L7 10.5 3 12.9l1-4.5-3.4-3 4.5-.4z"/>
  <use href="#s" x="16"/><use href="#s" x="32"/><use href="#s" x="48"/><use href="#s" x="64"/></g></svg>
</div>
<p class="abs quote">“Lorem ipsum dolor sit amet, consectetur adipiscing elit. Mauris interdum velit vitae nulla molestie eu commodo nulla dapib us. Donec id sollicitudin urna. Integer at dui ac leo fermentum varius eleifend ut.”</p>
<div class="abs author">Mara Ellison</div>
<div class="abs avatars" role="img" aria-label="Row of small customer portrait photos"></div>

<footer class="abs footer">
  <div class="abs flogo"><span class="brand-dot" style="width:18px;height:18px;background:#777"></span><span>Valewick Response Academy</span></div>
  <h4 style="left:220px">Let's Talk</h4>
  <p style="left:215px">hello@valewickacademy.com<br>Phone:+43 (0) 4521 806 337</p>
  <h4 style="left:387px">Find Us</h4>
  <p style="left:390px;top:43px">Address 4280 Brindle Ave #310<br>London 98712 , England</p>
  <h4 style="left:561px">Follow Us</h4>
  <div class="social" aria-label="Social links">
    <i style="background:#2ea3e0"></i><i style="background:#f08a1c"></i><i style="background:#3b5aa8"></i><i style="background:#e0293a"></i><i style="background:#444"></i>
  </div>
  <div class="frule"></div>
  <span class="copy">Copyright © 2015 Valewick Response Academy. All rights reserved.</span>
  <span class="flinks"><span>Home</span><span>Class Calender</span><span>Certification Classes</span><span>Classes for Groups</span><span>About Us</span><span>Policies</span><span>Medesto</span></span>
  <span class="code">C4</span>
</footer>
<div class="abs bottomline"></div>
</body>
</html>
```